4D Cradle Glimpse Luxury Ultrasound Billboard

Design a HIGH-END, MODERN billboard for my private prenatal ultrasound studio, 4D Cradle Glimpse, located in Pace, Florida.
This billboard will be viewed by drivers traveling at highway speeds, so it must be extremely clean, simple, and readable within 6 seconds.
About My Business
4D Cradle Glimpse is a private prenatal ultrasound studio specializing in:
Highest technology 4D/HD Ultrasounds
Early Gender Determination
Pregnancy Confirmation
I have been serving families for nearly 10 years and is known for creating a memorable experience, not just an ultrasound appointment.
Design Style
I DO NOT want:
Flowers
Leaves
Swirls
Glitter
Hearts everywhere
Busy backgrounds
Generic maternity stock graphics
I DO want:
Modern
Luxury
Upscale
Clean
Professional
Eye-catching
Premium medical spa feel
Colors
Use colors from my logo:
LOGO Green ( or a deep green)
Black
White
Soft Gold accents
Images:
Incorporate my professional headshot in a clean, modern way, logo, and the ultrasound images
Text
Keep wording minimal.
Primary Headline ( OPEN TO IDEAS) :
EXAMPLES ( WOULD RATHER SOMETHING MORE CATCHY)
" ADVANCED IMAGING. UNFORGETTABLE MOMENTS"
"MEET YOUR BABY BEFORE BIRTH"
Under headline:
4D Ultrasound • Early Gender • Pregnancy Confirmation
Business Name:
4D Cradle Glimpse
Private Prenatal Ultrasound Studio
Phone Number:
850-471-5923
Important
This billboard must be readable in 5–6 seconds from a moving vehicle.
Less text is better.
The phone number and business name must be visible from a distance.
The design should feel like a premium brand that immediately tells expecting parents:
“This is where I go to see my baby.”
Files Provided
Official logo
Headshot
Ultrasound images
Don’t make this look like a medical office billboard.
Make it look like a luxury baby experience billboard. That’s what separates 4D Cradle Glimpse from hospitals, OB offices, and all the new studios popping up around you. The emotional connection is what gets moms to book. ❤️
Billboard Size - 10.6” x 36”

```html
<!DOCTYPE html>
<html lang="en">
<head>
<meta charset="UTF-8">
<title>4D Cradle Glimpse Billboard</title>
<link href="https://fonts.googleapis.com/css2?family=Anton&family=Kaushan+Script&family=Oswald:wght@500;600&family=Playfair+Display:wght@700;800&display=swap" rel="stylesheet">
<style>
  :root {
    --green: #2d4023;
    --green-deep: #233319;
    --gold: #d9a52a;
    --white: #ffffff;
    --ink: #1e2a17;
    --stage: #e9ebe6;
  }
  * { box-sizing: border-box; margin: 0; padding: 0; }
  html, body { width: 1200px; height: 675px; overflow: hidden; background: var(--stage); }
  .billboard {
    position: absolute; left: 20px; top: 167px;
    width: 1160px; height: 340px;
    background: var(--white); overflow: hidden;
  }
  .headshot {
    position: absolute; left: 0; top: 0; width: 330px; height: 240px;
    background: linear-gradient(90deg, #dcdcd8 0%, #cfc9bd 35%, #3f5230 55%, #e9e9e6 80%, #ffffff 100%);
  }
  .phone-band {
    position: absolute; left: 0; top: 228px; width: 1160px; height: 112px;
    background: var(--green);
  }
  .brand-card {
    position: absolute; left: 12px; top: 200px; width: 296px; height: 128px;
    background: var(--white); border: 4px solid var(--green); border-radius: 14px;
    display: flex; flex-direction: column; align-items: center; justify-content: center; gap: 10px;
  }
  .brand-name {
    font-family: "Playfair Display", serif; font-weight: 700; font-size: 30px;
    color: var(--green); line-height: 1;
  }
  .brand-tag {
    font-family: "Oswald", sans-serif; font-weight: 500; font-size: 13px;
    letter-spacing: 0.08em; color: var(--ink);
    border-top: 1.5px solid var(--gold); padding-top: 6px;
  }
  .headline {
    position: absolute; left: 340px; top: 18px;
    font-family: "Playfair Display", serif; font-weight: 800; font-size: 58px;
    color: var(--ink); line-height: 1; white-space: nowrap;
  }
  .subhead {
    position: absolute; left: 380px; top: 86px;
    font-family: "Kaushan Script", cursive; font-size: 42px;
    color: var(--gold); line-height: 1; white-space: nowrap;
  }
  .services { position: absolute; left: 338px; top: 152px; display: flex; gap: 32px; list-style: none; }
  .service { display: flex; align-items: center; gap: 9px; }
  .service-icon { width: 52px; height: 52px; flex: none; }
  .service-label {
    font-family: "Oswald", sans-serif; font-weight: 500; font-size: 17px;
    line-height: 1.05; color: var(--ink); text-transform: uppercase;
  }
  .service-label b { display: block; font-weight: 600; color: var(--gold); font-size: 19px; }
  .phone {
    position: absolute; left: 336px; top: 230px;
    font-family: "Anton", sans-serif; font-size: 92px; line-height: 1.1;
    color: var(--white); letter-spacing: 0.01em; white-space: nowrap;
  }
  .scan-panel {
    position: absolute; left: 898px; top: 10px; width: 250px; height: 318px;
    background: var(--white);
  }
  .scan-frame {
    position: absolute; left: 4px; top: 4px; width: 242px; height: 270px;
    border: 8px solid var(--green); background: var(--green);
  }
  .scan-image {
    width: 100%; height: 100%;
    background: radial-gradient(circle at 50% 45%, #b9704f 0%, #8e4a33 45%, #4a1f14 100%);
  }
  .scan-strip {
    position: absolute; left: 4px; top: 284px; width: 242px; height: 16px;
    background: repeating-linear-gradient(90deg, var(--green) 0 5px, var(--white) 5px 8px);
  }
</style>
</head>
<body>
  <div class="billboard">
    <div class="headshot" role="img" aria-label="Professional headshot of the studio owner in green scrubs in her ultrasound room"></div>
    <div class="phone-band"></div>

    <h1 class="headline">Advanced Imaging</h1>
    <p class="subhead">Unforgettable Moments</p>

    <ul class="services">
      <li class="service">
        <svg class="service-icon" viewBox="0 0 52 52" aria-hidden="true">
          <circle cx="26" cy="26" r="26" fill="var(--green)"/>
          <rect x="13" y="15" width="22" height="16" rx="2" fill="none" stroke="#fff" stroke-width="2.5"/>
          <line x1="24" y1="31" x2="24" y2="37" stroke="#fff" stroke-width="2.5"/>
          <line x1="18" y1="37" x2="30" y2="37" stroke="#fff" stroke-width="2.5"/>
          <rect x="37" y="20" width="5" height="14" rx="2" fill="#fff"/>
        </svg>
        <span class="service-label"><b>4D</b>Ultrasound</span>
      </li>
      <li class="service">
        <svg class="service-icon" viewBox="0 0 52 52" aria-hidden="true">
          <circle cx="26" cy="26" r="26" fill="var(--green)"/>
          <circle cx="22" cy="29" r="7" fill="none" stroke="#fff" stroke-width="2.5"/>
          <line x1="22" y1="36" x2="22" y2="43" stroke="#fff" stroke-width="2.5"/>
          <circle cx="30" cy="22" r="7" fill="none" stroke="#fff" stroke-width="2.5"/>
          <path d="M35 17 L40 12 M35 12 H40 V17" fill="none" stroke="#fff" stroke-width="2.5"/>
        </svg>
        <span class="service-label"><b>Early</b>Gender</span>
      </li>
      <li class="service">
        <svg class="service-icon" viewBox="0 0 52 52" aria-hidden="true">
          <circle cx="26" cy="26" r="26" fill="var(--green)"/>
          <rect x="19" y="12" width="14" height="28" rx="4" fill="none" stroke="#fff" stroke-width="2.5"/>
          <line x1="26" y1="20" x2="26" y2="32" stroke="#fff" stroke-width="2.5"/>
          <line x1="20" y1="26" x2="32" y2="26" stroke="#fff" stroke-width="2.5"/>
        </svg>
        <span class="service-label"><b>Pregnancy</b>Confirmation</span>
      </li>
    </ul>

    <div class="brand-card">
      <span class="brand-name">4D Cradle Glimpse</span>
      <span class="brand-tag">PRENATAL ULTRASOUND STUDIO</span>
    </div>

    <p class="phone">850-471-5923</p>

    <div class="scan-panel">
      <div class="scan-frame">
        <div class="scan-image" role="img" aria-label="4D ultrasound image of twin babies face to face"></div>
      </div>
      <div class="scan-strip"></div>
    </div>
  </div>
</body>
</html>
```